Podiatry clinic requires a modern revamp and editing of existing website.

I would like a fresh new look and updated information for my current business website. An easy to navigate site with prominent address and phone number for call to action. We are a podiatry clinic that focuses on general and sports podiatry.
I would like 4 pages; including Home page, About Us, Services & Contact.
www.brambleridgepodiatry.net

Target Market(s)

Active working professionals.

Industry/Entity Type

Medical

Coding

Coded - Design and coding required

Number of Pages Required

4 page

Font styles to use
Sans Serif

Colors
6b449b

Requirements
Must have
• A modern look with logo and active images; clean and uncluttered. Visible phone number and address for call to action.
• 4 pages - Home, About Us, Services, Contact.
• Home page - update address & service logos.
• About Us - update of personal information.
• Services - Revamp of existing page.
• Contact page to include Google map, email & phone number.
Nice to have
• Ability to add content easily; eg. a blog or adding video onto Home page.
• Link to Online page.

```html
<!DOCTYPE html>
<html lang="en">
<head>
<meta charset="utf-8">
<title>Bramble Ridge Podiatry</title>
<link rel="stylesheet" href="https://fonts.googleapis.com/css2?family=Open+Sans:wght@400;600;700&family=Raleway:wght@300;400;500;600&display=swap">
<style>
:root{
  --purple:#4a2e96;
  --purple-dark:#432a8a;
  --purple-bar:#5a3caa;
  --green:#7cc12f;
  --orange:#ef6a1c;
  --grey-bg:#efefef;
  --text:#555;
  --heading:#555;
  --white:#fff;
}
*{margin:0;padding:0;box-sizing:border-box}
html,body{width:1200px;height:2817px;overflow:hidden;background:var(--white)}
body{position:relative;font-family:"Open Sans",Arial,sans-serif;color:var(--text)}
.abs{position:absolute}
.centered{left:0;width:1200px;text-align:center}

/* Hero */
.hero{top:0;left:0;width:1200px;height:802px;
  background:linear-gradient(180deg,#dfe4f6 0%,#a9b6ea 30%,#5a70d0 55%,#2f3fa8 75%,#4a3aa0 100%)}
.topbar-line{top:112px;left:77px;width:1046px;height:1px;background:rgba(74,46,150,.25)}
.address{top:32px;left:77px;display:flex;gap:10px;color:var(--purple);font-size:21px;line-height:27px}
.call{top:28px;right:77px;display:flex;gap:14px;align-items:center;color:var(--purple)}
.call-icon{width:52px;height:52px;border:2px solid var(--purple);border-radius:50%;display:flex;align-items:center;justify-content:center}
.call small{display:block;font-family:"Raleway",sans-serif;font-size:18px}
.call strong{display:block;font-size:31px;font-weight:700;line-height:36px}
.brand{top:150px;left:0;width:1200px;display:flex;justify-content:center;align-items:center;gap:18px}
.brand-dot{width:70px;height:70px;border-radius:50%;background:var(--purple)}
.brand-name{font-family:"Open Sans",sans-serif;font-weight:600;font-size:46px;line-height:54px;color:var(--purple)}
.hero-title{top:430px;font-weight:700;font-size:46px;line-height:62px;color:var(--white)}
.btn{display:inline-block;background:var(--purple);color:var(--white);font-family:"Raleway",sans-serif;font-size:23px;border-radius:30px;text-align:center}
.hero-btn{top:578px;left:486px;width:228px;height:62px;line-height:62px;font-size:26px}

/* Navigation */
.nav{top:802px;left:0;width:1200px;height:62px;background:var(--purple)}
.nav a{position:absolute;top:0;height:62px;line-height:62px;color:var(--white);text-decoration:none;font-family:"Raleway",sans-serif;font-size:19px}
.nav a.active{background:var(--green);left:77px;width:124px;text-align:center}

/* Welcome */
.section-title{font-family:"Raleway",sans-serif;font-weight:400;font-size:44px;color:var(--heading)}
.section-title span{color:var(--purple)}
.welcome-title{top:912px}
.welcome-text{top:985px;left:180px;width:840px;text-align:center;font-size:16px;line-height:25px}
.welcome-text p+p{margin-top:25px}
.welcome-btn{top:1129px;left:505px;width:190px;height:51px;line-height:51px}

/* Enquiries */
.enquiry{top:1234px;left:77px;width:1046px;height:256px;background:var(--grey-bg);border-bottom:4px solid var(--purple);box-shadow:0 22px 24px -14px rgba(0,0,0,.3)}
.enquiry-arrow{top:1490px;left:586px;width:0;height:0;border-left:14px solid transparent;border-right:14px solid transparent;border-top:14px solid var(--purple)}
.enquiry-photo{top:0;right:0;width:175px;height:252px;background:linear-gradient(160deg,#f4e1d6,#e3b9a5 60%,#efefef)}
.enq-head{top:22px;left:0;width:1046px;text-align:center;font-family:"Raleway",sans-serif;font-size:40px;color:var(--orange)}
.enq-call{top:88px;left:0;width:1046px;display:flex;justify-content:center;align-items:center;gap:14px;font-family:"Raleway",sans-serif;font-size:29px;color:var(--green)}
.enq-call .ring{width:52px;height:52px;border:2px solid var(--green);border-radius:50%;display:flex;align-items:center;justify-content:center}
.enq-call strong{font-family:"Open Sans",sans-serif;font-weight:700;font-size:29px}
.enq-or{top:160px;left:0;width:1046px;text-align:center;font-size:20px}
.enq-mail{top:198px;left:0;width:1046px;text-align:center;font-size:22px;color:var(--purple)}

/* Services */
.services-title{top:1562px}
.divider{top:1642px;left:600px;width:1px;height:320px;background:#ddd}
.service-photo{width:182px;height:182px;border-radius:50%;border:2px solid var(--purple);top:1640px}
.service-name{top:1843px;width:545px;text-align:center;font-family:"Raleway",sans-serif;font-size:32px;color:var(--purple)}
.service-desc{top:1893px;width:545px;padding:0 60px;text-align:center;font-size:16px;line-height:27px}
.service-btn{top:1963px;width:190px;height:50px;line-height:50px}

/* Follow */
.follow{top:2081px;left:0;width:1200px;height:250px;background:var(--grey-bg)}
.follow-photo{top:0;left:0;width:375px;height:250px;background:linear-gradient(120deg,#efefef 0%,#f1d7c8 40%,#e6bba4 70%,#efefef 100%)}
.follow-title{top:28px}
.follow-dot{top:99px;left:408px;width:122px;height:122px;border-radius:50%;background:var(--white);border:2px solid #ddd;display:flex;align-items:center;justify-content:center}
.follow-dot span{width:60px;height:60px;border-radius:50%;background:var(--purple)}
.follow-name{top:104px;left:543px;font-family:"Raleway",sans-serif;font-size:24px;color:var(--purple)}
.follow-like{top:145px;left:545px;width:202px;height:61px;border:2px solid var(--purple);border-radius:4px;display:flex;align-items:center;justify-content:center;font-weight:700;font-size:21px;color:var(--purple)}

/* Partners */
.partners-title{top:2354px}
.partner{top:2428px;height:92px;border-radius:8px;background:#e6e3ef}

/* Footer */
.footer{top:2554px;left:0;width:1200px;height:207px;background:var(--purple-dark)}
.f-item{top:42px;width:400px;text-align:center;color:var(--white)}
.f-icon{width:68px;height:68px;border-radius:50%;background:var(--purple-bar);margin:0 auto 20px;display:flex;align-items:center;justify-content:center}
.f-item p{font-size:15px;line-height:25px}
.f-item p.phone{font-size:21px;font-weight:600}
.bottom{top:2761px;left:0;width:1200px;height:56px;background:var(--purple-bar);color:var(--white)}
.bottom p{position:absolute;left:77px;top:17px;font-size:15px}
.socials{position:absolute;right:77px;top:18px;display:flex;gap:22px}
.socials span{width:20px;height:20px;border-radius:50%;background:rgba(255,255,255,.75)}
</style>
</head>
<body>

<header class="abs hero" role="img" aria-label="Photo of bare feet resting on a boat rail above the blue sea">
</header>
<div class="abs topbar-line"></div>
<div class="abs address">
  <svg width="16" height="24" viewBox="0 0 16 24"><path d="M8 0a8 8 0 0 0-8 8c0 6 8 16 8 16s8-10 8-16a8 8 0 0 0-8-8zm0 11a3 3 0 1 1 0-6 3 3 0 0 1 0 6z" fill="#4a2e96"/></svg>
  <div>Suite 208 / 72 Ashgrove<br>Street Larkfield 3100</div>
</div>
<div class="abs call">
  <div class="call-icon"><svg width="24" height="24" viewBox="0 0 24 24"><path d="M6.6 10.8a15 15 0 0 0 6.6 6.6l2.2-2.2a1 1 0 0 1 1-.25 11.4 11.4 0 0 0 3.6.57 1 1 0 0 1 1 1V20a1 1 0 0 1-1 1A17 17 0 0 1 3 4a1 1 0 0 1 1-1h3.5a1 1 0 0 1 1 1c0 1.25.2 2.45.57 3.57a1 1 0 0 1-.25 1z" fill="#4a2e96"/></svg></div>
  <div><small>CALL US NOW!</small><strong>1300 555 014</strong></div>
</div>
<div class="abs brand">
  <span class="brand-dot"></span>
  <div class="brand-name">Bramble Ridge<br>Podiatry</div>
</div>
<h1 class="abs centered hero-title">QUALIFIED HEALTH<br>PROFESSIONALS</h1>
<a class="abs btn hero-btn">CONTACT US</a>

<nav class="abs nav">
  <a class="active">HOME</a>
  <a style="left:235px">ABOUT</a>
  <a style="left:374px">SERVICES</a>
  <a style="left:537px">CONTACT</a>
</nav>

<h2 class="abs centered section-title welcome-title">WELCOME TO <span>BRAMBLE RIDGE PODIATRY</span></h2>
<div class="abs welcome-text">
  <p>Bramble Ridge Podiatry is a Podiatry clinic in the heart of Larkfield CBD. We are located between Elm &amp; Harper Streets in the Harbourview Business Centre / Linden Hotel Complex.</p>
  <p>Our podiatrists are fully qualified health professionals who are able to diagnose, treat, manage or help to prevent all medical conditions that affect the feet and lower limb.</p>
</div>
<a class="abs btn welcome-btn">READ MORE</a>

<section class="abs enquiry">
  <div class="abs enquiry-photo" role="img" aria-label="Photo of hands caring for a foot"></div>
  <div class="abs enq-head">For Appointments or Enquiries</div>
  <div class="abs enq-call">Please call us on
    <span class="ring"><svg width="24" height="24" viewBox="0 0 24 24"><path d="M6.6 10.8a15 15 0 0 0 6.6 6.6l2.2-2.2a1 1 0 0 1 1-.25 11.4 11.4 0 0 0 3.6.57 1 1 0 0 1 1 1V20a1 1 0 0 1-1 1A17 17 0 0 1 3 4a1 1 0 0 1 1-1h3.5a1 1 0 0 1 1 1c0 1.25.2 2.45.57 3.57a1 1 0 0 1-.25 1z" fill="#7cc12f"/></svg></span>
    <strong>1300 555 014</strong></div>
  <div class="abs enq-or">OR</div>
  <div class="abs enq-mail">Email: <svg width="20" height="15" viewBox="0 0 20 15"><rect x="1" y="1" width="18" height="13" fill="none" stroke="#4a2e96" stroke-width="2"/><path d="M1 1l9 7 9-7" fill="none" stroke="#4a2e96" stroke-width="2"/></svg> info@brambleridgepodiatry.net</div>
</section>
<div class="abs enquiry-arrow"></div>

<h2 class="abs centered section-title services-title">SERVICES <span>WE PROVIDE</span></h2>
<div class="abs divider"></div>
<div class="abs service-photo" style="left:225px;background:radial-gradient(circle at 50% 60%,#f1d6c6,#c9b7c4 60%,#8f8fa8)" role="img" aria-label="Photo of a podiatrist examining a foot"></div>
<div class="abs service-photo" style="left:769px;background:radial-gradient(circle at 50% 55%,#f3ddcf,#e8c6b5 55%,#d8d2de)" role="img" aria-label="Photo of a nail treatment on a toe"></div>
<h3 class="abs service-name" style="left:44px">General Treatment</h3>
<p class="abs service-desc" style="left:44px">Nails, Corns, Callus, Warts, Skin Disorders, Heel pain / Heel Spurs / Arch pain - plantar Fasciitis</p>
<a class="abs btn service-btn" style="left:227px">READ MORE</a>
<h3 class="abs service-name" style="left:588px">Specialised Treatments</h3>
<p class="abs service-desc" style="left:588px">Diabetic Management, Nail Surgery, Biomechanical Assessment, Gait Analysis, Orthotic Therapy</p>
<a class="abs btn service-btn" style="left:773px">READ MORE</a>

<section class="abs follow">
  <div class="abs follow-photo" role="img" aria-label="Photo of a pair of bare feet"></div>
  <h2 class="abs centered section-title follow-title">FOLLOW <span>US</span></h2>
  <div class="abs follow-dot"><span></span></div>
  <div class="abs follow-name">Bramble Ridge Podiatry</div>
  <div class="abs follow-like">Like Us Online</div>
</section>

<h2 class="abs centered section-title partners-title">AS <span>SEEN IN</span></h2>
<div class="abs partner" style="left:79px;width:226px"></div>
<div class="abs partner" style="left:361px;width:236px"></div>
<div class="abs partner" style="left:644px;width:216px"></div>
<div class="abs partner" style="left:913px;width:210px"></div>

<footer class="abs footer">
  <div class="abs f-item" style="left:29px">
    <div class="f-icon"><svg width="18" height="26" viewBox="0 0 16 24"><path d="M8 0a8 8 0 0 0-8 8c0 6 8 16 8 16s8-10 8-16a8 8 0 0 0-8-8zm0 11a3 3 0 1 1 0-6 3 3 0 0 1 0 6z" fill="#fff"/></svg></div>
    <p>Suite 208 / 72 Ashgrove Street<br>Larkfield 3100</p>
  </div>
  <div class="abs f-item" style="left:400px">
    <div class="f-icon"><svg width="24" height="24" viewBox="0 0 24 24"><path d="M6.6 10.8a15 15 0 0 0 6.6 6.6l2.2-2.2a1 1 0 0 1 1-.25 11.4 11.4 0 0 0 3.6.57 1 1 0 0 1 1 1V20a1 1 0 0 1-1 1A17 17 0 0 1 3 4a1 1 0 0 1 1-1h3.5a1 1 0 0 1 1 1c0 1.25.2 2.45.57 3.57a1 1 0 0 1-.25 1z" fill="#fff"/></svg></div>
    <p class="phone">1300 555 014</p>
  </div>
  <div class="abs f-item" style="left:756px">
    <div class="f-icon"><svg width="24" height="18" viewBox="0 0 20 15"><rect x="1" y="1" width="18" height="13" fill="none" stroke="#fff" stroke-width="2"/><path d="M1 1l9 7 9-7" fill="none" stroke="#fff" stroke-width="2"/></svg></div>
    <p>info@brambleridgepodiatry.net</p>
  </div>
</footer>
<div class="abs bottom">
  <p>© Bramble Ridge Podiatry- 2016. All Rights Reserved.</p>
  <div class="socials"><span></span><span></span><span></span></div>
</div>

</body>
</html>
```